KTWG application splash screen

We need a 1024x768 image for use as an application splash screen.
The image will be displayed full screen on an 10 inch industrial PC 1024x768 screen while our application is launching. The image should convey that the application is "Waiting for connection to Wi-Fi access point..." and include a graphic of the industrial PC connected to the access point via an Ethernet cable. A list of troubleshooting steps should be included at the bottom of the image. The troubleshooting steps should not be the main focus of the image and should be shown in a smaller font (but still readable at 1024x768 displayed on a 10 inch screen).
I will include a mock up of the general idea of what we are looking for as well as image files for the industrial PC, a screenshot of our application to show on the PC's screen and the AP.
For general look and feel and a sense of corporate branding please review our website https://marrowgatesoilworks.example/. The splash screen should reflect corporate branding.
Target Market(s)
Users of our application
Industry/Entity Type
Agriculture
Look and feel

```html
<!DOCTYPE html>
<html lang="en">
<head>
<meta charset="utf-8">
<title>KTWG splash screen</title>
<link rel="stylesheet" href="https://fonts.googleapis.com/css2?family=Lexend:wght@400;500;600&family=Tinos&display=swap">
<style>
  :root {
    --bg: #000000;
    --green: #4cb06c;
    --green-pill: #5fb97a;
    --box: #1d3b25;
    --white: #ffffff;
    --device-dark: #2b2d30;
    --device-screen: #dfe7e2;
    --ap-white: #eceff1;
  }
  * { box-sizing: border-box; }
  html, body {
    margin: 0;
    padding: 0;
    width: 1200px;
    height: 1200px;
    overflow: hidden;
    background: var(--bg);
  }
  .splash {
    position: absolute;
    left: 0;
    top: 150px;
    width: 1200px;
    height: 900px;
    overflow: hidden;
    background: var(--bg);
    color: var(--white);
  }
  .title {
    position: absolute;
    left: 0; right: 0;
    top: 56px;
    margin: 0;
    text-align: center;
    font: 600 41px/1 "Lexend", sans-serif;
    color: var(--green);
    letter-spacing: 0.3px;
  }
  .device-photo {
    position: absolute;
    left: 47px; top: 164px;
    width: 352px; height: 279px;
    border-radius: 12px;
    background: var(--device-dark);
  }
  .device-photo .screen {
    position: absolute;
    left: 30px; top: 25px;
    width: 285px; height: 220px;
    background: linear-gradient(180deg, var(--device-screen), #b9d8c3);
  }
  .ap-photo {
    position: absolute;
    left: 1032px; top: 143px;
    width: 46px; height: 304px;
    border-radius: 10px;
    background: linear-gradient(90deg, #d7dbde, var(--ap-white));
  }
  .link {
    position: absolute;
    left: 0; top: 0;
  }
  .cable-label {
    position: absolute;
    left: 0; right: 0;
    top: 499px;
    text-align: center;
    font: 500 25px/1 "Lexend", sans-serif;
    letter-spacing: 1.5px;
  }
  .node-label {
    position: absolute;
    top: 545px;
    text-align: center;
    font: 500 28px/33px "Lexend", sans-serif;
    color: var(--green);
  }
  .node-label--pc { left: 49px; width: 300px; }
  .node-label--ap { left: 897px; width: 300px; }
  .node-label small {
    display: block;
    font: 400 20px/28px "Lexend", sans-serif;
    color: var(--white);
  }
  .help {
    font-family: "Tinos", serif;
  }
  .help-tag {
    position: absolute;
    left: 54px; top: 658px;
    width: 239px; height: 36px;
    border-radius: 6px;
    background: var(--green-pill);
    font-size: 21px;
    line-height: 36px;
    padding-left: 10px;
  }
  .help-list {
    position: absolute;
    left: 58px; top: 707px;
    margin: 0; padding: 0;
    list-style: none;
    font-size: 19px;
    line-height: 37px;
  }
  .help-list li::before {
    content: "";
    display: inline-block;
    width: 14px; height: 14px;
    border-radius: 50%;
    background: var(--green);
    margin-right: 6px;
    vertical-align: -1px;
  }
  .step {
    position: absolute;
    top: 781px;
    height: 95px;
    padding: 8px 14px 0 16px;
    border-radius: 6px;
    background: var(--box);
    font-size: 16.5px;
    line-height: 20.5px;
  }
  .step--1 { left: 80px; width: 276px; }
  .step--2 { left: 373px; width: 276px; }
  .step--3 { left: 666px; width: 241px; }
  .step--4 { left: 923px; width: 241px; }
</style>
</head>
<body>
  <main class="splash">
    <h1 class="title">Waiting for Connection to Wi-Fi access point...</h1>

    <div class="device-photo" role="img" aria-label="Industrial tractor cab PC showing the KTWG application with green bar gauges">
      <div class="screen"></div>
    </div>
    <div class="ap-photo" role="img" aria-label="White outdoor Wi-Fi access point with two antennas"></div>

    <svg class="link" width="1200" height="900" viewBox="0 0 1200 900" aria-hidden="true">
      <g fill="none" stroke="#ffffff" stroke-width="2">
        <circle cx="214" cy="457" r="9"/>
        <circle cx="1053" cy="457" r="9"/>
      </g>
      <g stroke="#ffffff" stroke-width="3.5" stroke-linecap="round" stroke-dasharray="0 8.5" fill="none">
        <path d="M214 471 V513 H452"/>
        <path d="M756 513 H1053 V471"/>
      </g>
    </svg>
    <div class="cable-label">ETHERNET CABLE</div>

    <div class="node-label node-label--pc">Tractor cab<br>computer</div>
    <div class="node-label node-label--ap">Wi-Fi Access Point<small>Northway AP-220 Outdoor</small></div>

    <section class="help">
      <div class="help-tag">Troubleshooting steps:</div>
      <ul class="help-list">
        <li>This screen should only be visible for a short time on boot.</li>
        <li>If this screen stays visible for more than a minute:</li>
      </ul>
      <div class="step step--1">Verify that the Wi-Fi Access Point (AP) powers up when this system does (indicated by a green light n the side of the AP).</div>
      <div class="step step--2">Check the Ethernet cable between this system and the AP for damage, and replace it if necessary.</div>
      <div class="step step--3">Power-cycle this system and wait for it to reboot fully.</div>
      <div class="step step--4">If the issue persists, contact KTWG support for further assistance.</div>
    </section>
  </main>
</body>
</html>
```